TREVAL BUILDWORKS, LLC Webpage portfolio

I want to create a Website that allows my potential clients to browse my Skilled work via before and after photos. I want the website to enhance the work that I provide and potentially drive new business, or at least solidify my work.
I also do 3D CAD and Modeling of New Spaces and it would be nice to show some of that work from pencil design to 3D modeling, which I feel may help give me more clients.

The website needs to show a solid carpenter/company with the skills to get any project completed.

Types of Jobs - Custom Carpentry & Finishes, Kitchens, Baths, Basements, Decks, Porches, Whole House Renovation - Skilled Craftsmanship (Hardwood Flooring, Floor and Wall Tile) and much more...

Target Market(s)

Residential Home Renovation, Kitchen and Bath Renovation, Home Improvement

Industry/Entity Type

Residential Construction

Number of Pages Required

5+ page

Font styles to use
Sans Serif
Script

Requirements
Must have
• Similar to Plinvo.com, except for Treval Buildworks.
• Must be inviting.
• My Services Offered
• A way to reach me or contact me for estimates with some sort of Screening Questionare.
Nice to have
• Inviting Colors
Should not have
• Not sure at this time

```html
<!DOCTYPE html>
<html lang="en">
<head>
<meta charset="utf-8">
<title>Treval Buildworks</title>
<link href="https://fonts.googleapis.com/css2?family=Julius+Sans+One&family=Questrial&display=swap" rel="stylesheet">
<style>
:root{
  --stripe-a:#2b2a29;
  --stripe-b:#1f1e1d;
  --bg-deep:#141414;
  --ink:#f2f2f2;
  --ink-soft:#cfcfcf;
  --muted:#9a9a9a;
  --draft-a:#a9a9a9;
  --draft-b:#8c8c8c;
  --grey-a:#8a8988;
  --grey-b:#5f5e5c;
  --wall:#8a5443;
  --cabinet:#a8774e;
  --window:#d9ddd6;
  --dining-wall:#8a4e22;
  --dining-dark:#3a2516;
  --table:#8c7a55;
  --hall-a:#d6d0c6;
  --hall-b:#a07f62;
}
*{margin:0;padding:0;box-sizing:border-box}
html,body{width:847px;height:1200px;overflow:hidden}
body{
  position:relative;
  font-family:'Questrial',sans-serif;
  color:var(--ink);
  background:repeating-linear-gradient(90deg,var(--stripe-a) 0 4px,var(--stripe-b) 4px 6px,var(--stripe-a) 6px 8px);
}
.abs{position:absolute}
.heading{font-family:'Julius Sans One',sans-serif;font-size:24px;line-height:30px;letter-spacing:.5px;font-weight:400;z-index:3}
.small{font-size:8px;line-height:10.3px;text-transform:uppercase;letter-spacing:.2px;z-index:3}
.brand{left:36px;top:40px;font-size:13px;color:var(--ink-soft);display:flex;align-items:center;gap:6px}
.brand .mark{width:11px;height:11px;background:var(--ink-soft)}
.nav{right:35px;top:55px;display:flex;gap:14px;font-size:10px;letter-spacing:.2px}
.phone{right:35px;top:13px;font-size:7.5px}
.socials{display:flex;gap:11px}
.socials span{width:7px;height:7px;border-radius:50%;background:var(--ink)}
.photo{position:absolute}
.services-draft{left:96px;top:106px;width:238px;height:353px;
  background:linear-gradient(180deg,var(--draft-a),var(--draft-b))}
.services-grey{left:334px;top:106px;width:240px;height:353px;
  background:radial-gradient(ellipse 45% 35% at 60% 52%,#a9a9a7,transparent 70%),
             linear-gradient(90deg,var(--grey-b),var(--grey-a) 40%,var(--grey-b))}
.services-kitchen{left:574px;top:106px;width:238px;height:353px;
  background:radial-gradient(ellipse 32% 34% at 45% 52%,var(--window),#b7b3a6 55%,transparent 80%),
             linear-gradient(180deg,transparent 78%,#6b4a32 82%,#4a3526),
             linear-gradient(90deg,#6d4536,var(--wall) 35%,var(--wall) 70%,var(--cabinet) 82%,#7a5a3e)}
.work-bg{left:96px;top:459px;width:717px;height:353px;
  background:radial-gradient(ellipse 60% 45% at 70% 85%,var(--table),transparent 75%),
             linear-gradient(160deg,var(--dining-wall) 0%,#6a3d1e 35%,var(--dining-dark) 60%,#4e3a25)}
.work-slide{left:96px;top:529px;width:342px;height:157px;
  background:linear-gradient(180deg,transparent 60%,rgba(150,100,70,.55)),
             linear-gradient(90deg,#9a9590,var(--hall-a) 40%,#e4e0d8 55%,var(--hall-b) 85%,#c9c4bb);z-index:2}
.testimonials-bg{left:96px;top:812px;width:717px;height:388px;background:var(--bg-deep)}
.arrows{left:36px;top:675px;display:flex;gap:17px;z-index:3}
.quote{width:100px;text-align:right;top:990px}
.quote p{font-size:7.5px;line-height:10px;color:var(--ink-soft)}
.quote .name{margin-top:40px;font-size:11px;letter-spacing:.5px;color:var(--ink)}
.quote .role{font-size:7.5px;color:var(--ink)}
.quote .stars{margin-top:14px;font-size:8px;letter-spacing:3px;color:var(--muted)}
.cta{right:70px;top:1127px;font-family:'Julius Sans One',sans-serif;font-size:16px;color:var(--ink-soft)}
</style>
</head>
<body>
<header>
  <div class="abs brand"><span class="mark"></span>Treval Buildworks</div>
  <div class="abs socials" style="left:628px;top:17px"><span></span><span></span><span></span><span></span></div>
  <div class="abs phone">+8 (555) 010-42-17</div>
  <nav class="abs nav"><span>KITCHENS</span><span>BATHS</span><span>BASEMENTS</span><span>FINISHED CARPENTRY</span><span>DECKS &amp; PORCHES</span></nav>
</header>

<section class="services">
  <div class="photo services-draft" role="img" aria-label="Line drawing of a kitchen design"></div>
  <div class="photo services-grey" role="img" aria-label="Kitchen render in greyscale"></div>
  <div class="photo services-kitchen" role="img" aria-label="Finished kitchen with wood cabinets and window"></div>
  <h2 class="abs heading" style="left:35px;top:102px">MY<br>SERVICES</h2>
  <div class="abs small" style="left:35px;top:211px">3D CAD modelling of new<br>spaces</div>
  <div class="abs small" style="left:35px;top:241px">Custom<br>carpentry &amp; finishes,</div>
  <div class="abs small" style="left:35px;top:271px">Kitchens,<br>baths,<br>basements,<br>decks,<br>porches,</div>
  <div class="abs" style="left:35px;top:333px;font-size:11.5px;line-height:16px;z-index:3">WHOLE HOUSE<br>RENOVATION</div>
  <div class="abs small" style="left:35px;top:362px">Skilled craftsmanship<br>((hardwood flooring,<br>floor and wall tile)</div>
  <div class="abs small" style="left:35px;top:404px">and much more</div>
</section>

<section class="work">
  <div class="photo work-bg" role="img" aria-label="Dining table with stone top and wooden chairs"></div>
  <div class="photo work-slide" role="img" aria-label="Before photo of a hallway with tiled floor"></div>
  <h2 class="abs heading" style="left:35px;top:526px">BROWSE<br>MY WORK</h2>
  <div class="abs small" style="left:37px;top:634px">Brose my work in<br>before and after<br>photos</div>
  <div class="abs arrows">
    <svg width="9" height="9"><path d="M9 0 L0 4.5 L9 9Z" fill="#f2f2f2"/></svg>
    <svg width="9" height="9"><path d="M0 0 L9 4.5 L0 9Z" fill="#f2f2f2"/></svg>
  </div>
  <div class="abs socials" style="left:36px;top:789px;z-index:3"><span></span><span></span><span></span><span></span></div>
</section>

<section class="testimonials">
  <div class="photo testimonials-bg"></div>
  <h2 class="abs heading" style="left:35px;top:878px">CLIENTS<br>TESTIMONIALS</h2>
  <div class="abs small" style="left:35px;top:987px">Read what our happy<br>clients have to say<br>about our expertise and<br>services</div>
  <div class="abs quote" style="left:317px"><p>Lorem ipsum dolor<br>sit amet, consectetur<br>adipiscing elit. ..</p><div class="name">JOHN DOE</div><div class="role">Entrepreneur</div><div class="stars">★★★★★</div></div>
  <div class="abs quote" style="left:437px"><p>Lorem ipsum dolor<br>sit amet, consectetur<br>adipiscing elit. ..</p><div class="name">JOHN DOE</div><div class="role">Entrepreneur</div><div class="stars">★★★★★</div></div>
  <div class="abs quote" style="left:557px"><p>Lorem ipsum dolor<br>sit amet, consectetur<br>adipiscing elit. ..</p><div class="name">JOHN DOE</div><div class="role">Entrepreneur</div><div class="stars">★★★★★</div></div>
  <div class="abs quote" style="left:677px"><p>Lorem ipsum dolor<br>sit amet, consectetur<br>adipiscing elit. ..</p><div class="name">JOHN DOE</div><div class="role">Entrepreneur</div><div class="stars">★★★★★</div></div>
  <div class="abs socials" style="left:36px;top:1131px;z-index:3"><span></span><span></span><span></span><span></span></div>
  <div class="abs cta">REQUEST AN ESTIMATE</div>
</section>
</body>
</html>
```